Design a compelling Tarnwove Business Card that will drive people to my site

I want a business card that I can give to people—less to tell them who I am and more to direct them to my website. My website is a portal for Pelmor Aquatics Officials and a place for people who want to become Pelmor Aquatics Officials.
I am uploading my official company logo as well as a business card mockup that I did on my own. Please feel free to completely stray from this design.
I've included a screen recording of the homepage of my website as well.
Target Market(s)
Pelmor Aquatics Officials and people who desire to become one
Contact Information for Business Card
website url
Look and feel
Each slider illustrates characteristics of the customer's brand and the style your logo design should communicate.

```html
<!DOCTYPE html>
<html lang="en">
<head>
<meta charset="UTF-8">
<title>Tarnwove Business Card</title>
<link href="https://fonts.googleapis.com/css2?family=Montserrat:wght@400;600;700&display=swap" rel="stylesheet">
<style>
  :root {
    --stage: #d9dbe0;
    --brand-blue: #344e9f;
    --brand-blue-deep: #2b4593;
    --card-white: #ffffff;
    --card-white-shade: #eceef2;
    --ink-grey: #555a63;
    --rule-grey: #b9bec8;
  }
  * { margin: 0; padding: 0; box-sizing: border-box; }
  html, body {
    width: 1200px;
    height: 900px;
    overflow: hidden;
    background: var(--stage);
    font-family: "Montserrat", sans-serif;
  }
  .stage {
    width: 1200px;
    height: 900px;
    display: flex;
    flex-direction: column;
    align-items: center;
    justify-content: center;
    gap: 56px;
  }
  .card {
    width: 620px;
    height: 354px;
    border-radius: 30px;
    position: relative;
    box-shadow: 0 14px 30px rgba(40, 45, 60, 0.25);
    overflow: hidden;
  }
  .card--back {
    background: linear-gradient(135deg, var(--brand-blue-deep), var(--brand-blue));
    display: flex;
    align-items: center;
    justify-content: center;
  }
  .wordmark {
    display: flex;
    align-items: center;
    gap: 14px;
    font-weight: 700;
    letter-spacing: -0.5px;
    text-transform: lowercase;
  }
  .wordmark__dot {
    border-radius: 50%;
    flex: none;
  }
  .card--back .wordmark { color: var(--card-white); font-size: 68px; }
  .card--back .wordmark__dot { width: 30px; height: 30px; background: var(--card-white); }

  .card--front {
    background: linear-gradient(120deg, var(--card-white) 40%, var(--card-white-shade));
  }
  .card--front .wordmark {
    position: absolute;
    left: 44px;
    top: 58px;
    color: var(--brand-blue);
    font-size: 50px;
  }
  .card--front .wordmark__dot { width: 22px; height: 22px; background: var(--brand-blue); }

  .contact-block {
    position: absolute;
    right: 40px;
    bottom: 48px;
    display: flex;
    align-items: flex-end;
    gap: 20px;
  }
  .identity { text-align: right; }
  .identity__title {
    font-size: 15px;
    font-weight: 400;
    color: var(--ink-grey);
    letter-spacing: 0.3px;
  }
  .identity__name {
    font-size: 17px;
    font-weight: 700;
    color: var(--brand-blue);
    margin-top: 2px;
  }
  .divider {
    width: 1px;
    height: 82px;
    background: var(--rule-grey);
  }
  .contact-list { list-style: none; }
  .contact-list li {
    display: flex;
    align-items: center;
    gap: 9px;
    font-size: 14px;
    color: var(--ink-grey);
    line-height: 26px;
  }
  .contact-list svg { width: 14px; height: 14px; flex: none; }
</style>
</head>
<body>
<main class="stage">
  <section class="card card--back" aria-label="Card back">
    <div class="wordmark"><span class="wordmark__dot"></span><span>tarnwove</span></div>
  </section>

  <section class="card card--front" aria-label="Card front">
    <div class="wordmark"><span class="wordmark__dot"></span><span>tarnwove</span></div>

    <div class="contact-block">
      <div class="identity">
        <p class="identity__title">CEO &amp; Founder</p>
        <p class="identity__name">Marcus Feldane</p>
      </div>
      <span class="divider"></span>
      <ul class="contact-list">
        <li>
          <svg viewBox="0 0 16 16" aria-hidden="true"><path fill="#344e9f" d="M3.6 1.2l2.3 2.6-1.3 1.8c.9 2 2.6 3.7 4.6 4.6l1.8-1.3 2.6 2.3-1.4 2.6C6.6 13.4 2.6 9.4 1 3.6z"/></svg>
          (555) 014-2287
        </li>
        <li>
          <svg viewBox="0 0 16 16" aria-hidden="true"><rect x="1" y="3" width="14" height="10" fill="#344e9f"/><path d="M1.5 3.5L8 9l6.5-5.5" fill="none" stroke="#fff" stroke-width="1.3"/></svg>
          marcus@tarnwove.com
        </li>
        <li>
          <svg viewBox="0 0 16 16" aria-hidden="true"><g fill="none" stroke="#344e9f" stroke-width="1.3"><circle cx="8" cy="8" r="6.3"/><ellipse cx="8" cy="8" rx="2.8" ry="6.3"/><path d="M1.7 8h12.6"/></g></svg>
          www.tarnwove.com
        </li>
      </ul>
    </div>
  </section>
</main>
</body>
</html>
```